We are a recruitment company based in Norwich/Cambridge England.
I have included our company logo which we want to remain the same.

What we are looking for is a new creative Business card which will really stand out!!

Contact Information for Business Card

Harriet Dunmore
email: Harriet@plavex.co.uk
Address: Brackwell House
Fenmoor Enterprise Park
Partridge Way
Norwich
QB9 3KX
Tel:01632 960418

```html
<!DOCTYPE html>
<html lang="en">
<head>
<meta charset="utf-8">
<title>Plavex Business Card</title>
<link href="https://fonts.googleapis.com/css2?family=Montserrat:wght@600;700&family=Open+Sans:wght@400;600&display=swap" rel="stylesheet">
<style>
  :root {
    --backdrop: #3a3430;
    --card: #0e0e0e;
    --green: #7dc242;
    --grey: #9a9a9f;
    --text: #d9d9d9;
    --rule: #4a4a4a;
  }
  * { margin: 0; padding: 0; box-sizing: border-box; }
  html, body { width: 1200px; height: 900px; overflow: hidden; }
  body {
    background: var(--backdrop);
    font-family: "Open Sans", Arial, sans-serif;
    position: relative;
  }
  .card {
    position: absolute;
    width: 520px;
    height: 300px;
    background: var(--card);
    border-radius: 3px;
    box-shadow: 0 12px 30px rgba(0,0,0,0.45);
  }
  .card--details { left: 50px; top: 320px; }
  .card--brand { left: 630px; top: 280px; }

  .brand-panel {
    position: absolute;
    left: 40px; top: 70px;
    width: 200px;
    display: flex; flex-direction: column; align-items: center; gap: 18px;
  }
  .brand-panel__dot {
    width: 110px; height: 110px; border-radius: 50%;
    background: var(--grey);
  }
  .brand-panel__name {
    font-family: "Montserrat", Arial, sans-serif;
    font-weight: 700; font-size: 38px; color: var(--green);
  }

  .divider {
    position: absolute; left: 262px; top: 45px;
    width: 1px; height: 210px; background: var(--rule);
  }
  .contact {
    position: absolute; left: 282px; top: 48px;
  }
  .contact__name {
    font-family: "Montserrat", Arial, sans-serif;
    font-weight: 700; font-size: 19px; letter-spacing: 0.3px; text-transform: uppercase;
  }
  .contact__first { color: var(--green); }
  .contact__last { color: var(--grey); }
  .contact__role { font-size: 12.5px; color: var(--text); margin-bottom: 12px; }
  .contact__list { list-style: none; }
  .contact__item {
    display: flex; align-items: flex-start; gap: 8px;
    font-size: 13px; line-height: 19px; color: var(--text);
  }
  .contact__icon { width: 11px; height: 11px; margin-top: 4px; flex: none; fill: var(--green); }
  .contact__address { margin-top: 4px; }

  .brand-front {
    position: absolute; left: 120px; top: 105px;
    display: flex; align-items: center; gap: 16px;
  }
  .brand-front__dot {
    width: 80px; height: 80px; border-radius: 50%; background: var(--grey);
  }
  .brand-front__name {
    font-family: "Montserrat", Arial, sans-serif;
    font-weight: 700; font-size: 50px; color: var(--green); line-height: 1;
  }
  .brand-front__tagline {
    font-size: 10px; letter-spacing: 3px; color: var(--grey); margin-top: 6px;
  }
</style>
</head>
<body>
  <section class="card card--details">
    <div class="brand-panel">
      <span class="brand-panel__dot"></span>
      <span class="brand-panel__name">Plavex</span>
    </div>
    <div class="divider"></div>
    <div class="contact">
      <p class="contact__name"><span class="contact__first">Harriet</span> <span class="contact__last">Dunmore</span></p>
      <p class="contact__role">Managing Director</p>
      <ul class="contact__list">
        <li class="contact__item">
          <svg class="contact__icon" viewBox="0 0 12 12"><path d="M2.5 0.5l2 2.2-1 1.4c0.8 1.7 1.8 2.7 3.4 3.4l1.4-1 2.2 2-1.2 2.5C5 10.7 1.3 7 0 2z"/></svg>
          01632 960418
        </li>
        <li class="contact__item">
          <svg class="contact__icon" viewBox="0 0 12 12"><path d="M0 2h12v8H0z M1 3l5 3.5L11 3" fill="var(--green)" stroke="#0e0e0e" stroke-width="0.9"/></svg>
          Harriet@plavex.co.uk
        </li>
        <li class="contact__item">
          <svg class="contact__icon" viewBox="0 0 12 12"><circle cx="6" cy="6" r="5.5"/></svg>
          www.plavex.co.uk
        </li>
        <li class="contact__item contact__address">
          <svg class="contact__icon" viewBox="0 0 12 12"><path d="M6 0a4 4 0 0 1 4 4c0 3-4 8-4 8S2 7 2 4a4 4 0 0 1 4-4z"/></svg>
          <span>Brackwell House, Fenmoor Enterprise Park,<br>Partridge Way, Norwich, QB9 3KX</span>
        </li>
      </ul>
    </div>
  </section>

  <section class="card card--brand">
    <div class="brand-front">
      <span class="brand-front__dot"></span>
      <div>
        <p class="brand-front__name">Plavex</p>
        <p class="brand-front__tagline">Technology Recruitment</p>
      </div>
    </div>
  </section>
</body>
</html>
```